Cedar-Rock Harvest Chapel WL- Theme for 2022

We, Cedar-Rock Harvest Chapel of Willow Landing, need a design for a 4' x 6' banner that will be placed on two walls in the main sanctuary. The banner is to communicate/advertise the church's theme for 2022, "He Will Make All Things New: A New You - 2022" Revelations 21:5. The design should include our logo and church name. Use the color purple. We have not worshipped in our church building since 2020 due to the COVID pandemic. This banner should be reflective of change, newness as we plan to re-enter the building this spring. Our congregation demographic is 95% African American, 5% Hispanic. Our home base is Tampa, Florida (USA), but we have a large social media following, primarily due to the pandemic.

Target Market(s)

Church members, Ages 1-99; male and female

Industry/Entity Type

Religious

Font styles to use
Serif

Colors
0094D4
00A9DD
6FCCEA
C7EBF8
E9F6FB
00AB8E
00BBA5
67D7C9
C6EFE9
E9F9F6
6B429C
8869AF
B7A5CE
E3DAEB
F3F0F8

Requirements
Must have
• Theme, scripture, church logo and color purple

```html
<!DOCTYPE html>
<html lang="en">
<head>
<meta charset="utf-8">
<title>Cedar-Rock Harvest Chapel WL – A New You 2022 Banner</title>
<link rel="stylesheet" href="https://fonts.googleapis.com/css2?family=Outfit:wght@400;500;600;700;800&display=swap">
<style>
  :root {
    --page-bg: #e8e8e8;
    --ink: #1a1a1a;
    --purple: #8a14d0;
    --purple-deep: #5e0e9c;
    --gold: #f2b705;
    --white: #ffffff;
    --wall-grey: #b9b6bd;
    --scene-top: #6a4a8e;
    --scene-bottom: #c89a6a;
  }
  * { margin: 0; padding: 0; box-sizing: border-box; }
  html, body {
    width: 800px; height: 1200px; overflow: hidden;
    background: var(--page-bg);
    font-family: "Outfit", sans-serif;
  }
  .banner {
    position: absolute; left: 30px; top: 353px;
    width: 740px; height: 493px;
    overflow: hidden;
    background: linear-gradient(90deg, var(--white) 0%, #f4f4f5 35%, #d3d1d6 60%, var(--wall-grey) 100%);
    box-shadow: 0 6px 24px rgba(0,0,0,0.12);
  }
  .scene-photo {
    position: absolute; left: 372px; top: 58px; width: 368px; height: 435px;
    background: linear-gradient(180deg, var(--scene-top) 0%, #8f7aa6 45%, #d9c4a8 72%, var(--scene-bottom) 100%);
  }
  .brand {
    position: absolute; left: 26px; top: 24px;
    display: flex; align-items: center; gap: 12px;
  }
  .brand-dot { width: 82px; height: 82px; border-radius: 50%; background: var(--purple); flex: none; }
  .brand-name { font-size: 16px; font-weight: 600; color: var(--ink); }
  .theme { position: absolute; left: 26px; top: 114px; line-height: 1; }
  .theme-lead { font-size: 30px; font-weight: 500; color: var(--ink); letter-spacing: -0.3px; }
  .theme-main { font-size: 42px; font-weight: 800; color: var(--ink); letter-spacing: -1.2px; margin-top: 3px; }
  .theme-year { font-size: 42px; font-weight: 800; color: var(--purple); letter-spacing: -1.2px; margin-top: -2px; }
  .scripture {
    position: absolute; left: 26px; top: 228px;
    height: 28px; padding: 0 16px;
    background: var(--gold); border-radius: 14px;
    font-size: 20px; font-weight: 600; color: var(--ink);
    line-height: 28px;
  }
  .church-name {
    position: absolute; left: 26px; top: 264px;
    font-size: 22px; font-weight: 500; color: var(--ink); line-height: 29px;
  }
  .wave { position: absolute; left: 0; top: 0; width: 740px; height: 493px; }
  .cta { position: absolute; left: 28px; top: 412px; }
  .cta-line { font-size: 34px; font-weight: 800; color: var(--white); letter-spacing: -0.9px; line-height: 1; }
  .cta-line .highlight { color: var(--gold); }
  .cta-url { font-size: 15px; font-weight: 600; color: var(--white); letter-spacing: 3.5px; margin-top: 5px; }
</style>
</head>
<body>
  <main class="banner">
    <div class="scene-photo" role="img" aria-label="Photo of open purple double doors revealing a bright church sanctuary, light spilling onto a wooden floor"></div>

    <div class="brand">
      <span class="brand-dot"></span>
      <span class="brand-name">Cedar-Rock Harvest Chapel WL</span>
    </div>

    <h1 class="theme">
      <div class="theme-lead">HE WILL MAKE</div>
      <div class="theme-main">ALL THINGS NEW</div>
      <div class="theme-year">A NEW YOU 2022</div>
    </h1>

    <div class="scripture">REVELATIONS 21:5</div>

    <p class="church-name">Cedar-Rock<br>Harvest Chapel<br>Of Willow Landing</p>

    <svg class="wave" viewBox="0 0 740 493" aria-hidden="true">
      <defs>
        <linearGradient id="band-purple" x1="0" y1="0" x2="0" y2="1">
          <stop offset="0" stop-color="#9a1ee0"/>
          <stop offset="1" stop-color="#5e0e9c"/>
        </linearGradient>
      </defs>
      <path d="M0,370 C150,356 300,368 420,408 C520,440 600,456 660,450 C700,446 725,432 740,416 L740,493 L0,493 Z" fill="var(--gold)"/>
      <path d="M0,400 C150,376 300,386 420,420 C520,450 600,478 660,478 C700,478 725,470 740,462 L740,493 L0,493 Z" fill="url(#band-purple)" stroke="var(--white)" stroke-width="3"/>
    </svg>

    <div class="cta">
      <div class="cta-line">WE ARE <span class="highlight">OPEN NOW</span></div>
      <div class="cta-url">www.crhcwl.org</div>
    </div>
  </main>
</body>
</html>
```